Telecommunications/Power civil contractor needs business card design

Were a new telecommunications/power underground civil contractor that is looking for a new business card design. Our company colours are silver or grey and orange. Feel free to use the white background logo or the black background logo.

Target Market(s)

Local contractors, utility companies, private sector mining/energy companies, developers.

Industry/Entity Type

Telecommunications

Contact Information for Business Card

Each card will need the following info:
Persons name:
Title:
E-mail:
Phone number:
Shop Address:
Mailing Address:

Requirements
Must have
• Each card will need the following info:
• Persons name:
• Title:
• E-mail:
• Phone number:
• Shop Address:
• Mailing Address:

```html
<!DOCTYPE html>
<html lang="en">
<head>
<meta charset="utf-8">
<title>Torch Line Contracting Inc – Business Card</title>
<link rel="stylesheet" href="https://fonts.googleapis.com/css2?family=Open+Sans:wght@400;700;800&display=swap">
<style>
  :root {
    --backdrop: #c9ccd6;
    --card-white: #ffffff;
    --brand-orange: #f15a22;
    --brand-grey: #8a8a8c;
    --swoosh-grey: #a9a9ab;
    --title-grey: #5b5f66;
    --card-black: #141414;
    --text-white: #ffffff;
  }
  * { box-sizing: border-box; margin: 0; padding: 0; }
  html, body {
    width: 1200px; height: 797px; overflow: hidden;
    background: var(--backdrop);
    font-family: "Open Sans", Arial, sans-serif;
  }
  .stage {
    position: relative; width: 1200px; height: 797px;
    display: flex; align-items: center; justify-content: center; gap: 60px;
  }
  .card {
    position: relative; width: 520px; height: 300px;
    border-radius: 3px; overflow: hidden;
    box-shadow: 0 10px 22px rgba(40, 44, 60, 0.25);
  }
  .card-front { background: var(--card-white); }
  .card-front .front-art { position: absolute; inset: 0; }

  .brand-lockup {
    position: absolute; left: 28px; top: 112px; width: 210px;
    display: flex; flex-direction: column; align-items: center; gap: 12px;
  }
  .brand-ring {
    width: 56px; height: 56px; border-radius: 50%;
    border: 4px solid var(--brand-orange);
  }
  .brand-name {
    color: var(--brand-orange); font-weight: 800;
    font-size: 17px; line-height: 1.15; text-align: center;
    text-transform: uppercase; letter-spacing: 0.5px;
  }

  .contact-block {
    position: absolute; right: 24px; top: 26px;
    text-align: right; color: var(--text-white);
    font-size: 12.5px; line-height: 1.4;
  }
  .contact-name { font-weight: 700; font-size: 15px; }
  .contact-title { color: var(--title-grey); font-size: 13.5px; }
  .contact-address { margin-top: 14px; }
  .contact-lines { margin-top: 16px; }
  .contact-line { display: flex; justify-content: flex-end; align-items: center; gap: 5px; }
  .contact-icon { width: 12px; height: 12px; flex: none; }

  .card-back {
    background: var(--card-black);
    display: flex; flex-direction: column; align-items: center; justify-content: center; gap: 14px;
  }
  .back-ring {
    width: 110px; height: 110px; border-radius: 50%;
    border: 6px solid var(--brand-orange);
  }
  .back-name {
    color: var(--brand-orange); font-weight: 800; font-size: 15px;
    text-transform: uppercase; letter-spacing: 1px;
  }
</style>
</head>
<body>
<main class="stage">
  <section class="card card-front">
    <svg class="front-art" viewBox="0 0 520 300" width="520" height="300" aria-hidden="true">
      <path d="M236,0 C282,60 300,160 346,300 L520,300 L520,0 Z" fill="var(--brand-orange)"/>
      <path d="M252,0 C282,50 294,90 300,120" fill="none" stroke="var(--card-white)" stroke-width="3"/>
      <path d="M270,160 C300,200 300,250 250,300 L346,300 C320,240 300,200 270,160 Z" fill="var(--swoosh-grey)"/>
    </svg>

    <div class="brand-lockup">
      <div class="brand-ring"></div>
      <div class="brand-name">Torch Line<br>Contracting Inc</div>
    </div>

    <div class="contact-block">
      <div class="contact-name">Dalton Reyes</div>
      <div class="contact-title">Managing Director</div>
      <div class="contact-address">N. 12 Alder Avenue,<br>Suite 200, Tacoma,<br>WA 55555</div>
      <div class="contact-lines">
        <div class="contact-line">555.010.2040
          <svg class="contact-icon" viewBox="0 0 12 12" aria-hidden="true">
            <circle cx="6" cy="6" r="6" fill="var(--text-white)"/>
            <path d="M4,3 L5,3 L5.6,4.6 L4.9,5.2 C5.3,6 6,6.7 6.8,7.1 L7.4,6.4 L9,7 L9,8 C9,8.5 8.5,9 8,9 C5.2,8.8 3.2,6.8 3,4 C3,3.5 3.5,3 4,3 Z" fill="var(--brand-orange)"/>
          </svg>
        </div>
        <div class="contact-line">info@torchlinecivil.com
          <svg class="contact-icon" viewBox="0 0 12 12" aria-hidden="true">
            <circle cx="6" cy="6" r="6" fill="var(--text-white)"/>
            <rect x="3" y="4" width="6" height="4.2" fill="var(--brand-orange)"/>
            <path d="M3,4 L6,6.4 L9,4" fill="none" stroke="var(--text-white)" stroke-width="0.7"/>
          </svg>
        </div>
      </div>
    </div>
  </section>

  <section class="card card-back">
    <div class="back-ring"></div>
    <div class="back-name">Torch Line Contracting Inc</div>
  </section>
</main>
</body>
</html>
```